Existing Website Requiring new Pages

I have an existing word press website that was built using elementor.
Website: www.tallowcrestcare.com.au
I require the Vacancies page (https://www.tallowcrestcare.com.au/vacancies/) to be modified to display our new properties along with minor tweaks to how the information is presented.
The vacancies to be displayed are the exactly the same as those that are located on the homepage of QMR website (https://qmr.org.au/)
The new pages that link off the Vacancies tab will require custom design.
There are roughly 8 pages/properties to be incorporated. i wish for the design to be very similar to that displayed in the following link; https://www.polunda.com.au/vacancies/merrylands
Along with this the back end has not been updated for the last 3 years so it also requires some maintenance.
Website is in the disability industry and the custom pages will display information relative to Property Vacancies.
I have attached a ZIP file with some design guides, the information for each of the properties (which will need to be modified to show our business name Tallowcrest Care) and the example of how it is to look based off the Polunda website.
If you guys have any suggestions or ideas on how to make this more presentable or possible i'm open to your ideas.
Target Market(s)
People looking for SDA properties custom built for people with a disability
Industry/Entity Type
Disability
Coding
Coded - Design and coding required
Number of Pages Required
5+ page

```html
<!DOCTYPE html>
<html lang="en">
<head>
<meta charset="utf-8">
<title>Vacancies – Tallowcrest Care</title>
<link href="https://fonts.googleapis.com/css2?family=Lato:wght@400;700&family=Montserrat:wght@400;500;600;700&display=swap" rel="stylesheet">
<style>
:root{
  --orange:#f98e52;
  --ink:#3a3a3a;
  --text:#4a4a4a;
  --muted:#8a8a8a;
  --purple:#7d5cc6;
  --pink:#ea3d8c;
  --sky:#4bb2e3;
  --amber:#f7894a;
  --teal:#26c4a8;
  --rose:#ef2b6c;
  --footer-bg:#ffffff;
  --bar:#1f1f1f;
}
*{margin:0;padding:0;box-sizing:border-box}
html,body{width:1200px;height:2707px;overflow:hidden;background:#fff}
body{position:relative;font-family:'Lato',sans-serif;color:var(--text)}
.abs{position:absolute}

.site-header{position:absolute;left:0;top:0;width:1200px;height:136px;background:#fff}
.brand{position:absolute;left:112px;top:50px;font-family:'Lato',sans-serif;font-size:26px;font-weight:400;color:var(--orange);letter-spacing:.5px;display:flex;align-items:center;gap:10px}
.brand .dot{width:22px;height:22px;border-radius:50%;background:var(--pink)}
.main-nav{position:absolute;right:113px;top:60px;display:flex;gap:25px;font-family:'Montserrat',sans-serif;font-size:11px;font-weight:600;letter-spacing:.6px;text-transform:uppercase;color:#333}
.main-nav .active{color:var(--orange)}

.hero{position:absolute;left:0;top:136px;width:1200px;height:557px;overflow:hidden}
.hero-photo{position:absolute;inset:0;background:linear-gradient(100deg,#6e4a35 0%,#8b6a52 40%,#a88a70 70%,#5c4a3e 100%)}
.hero svg{position:absolute;left:0;top:0}
.hero h1{position:absolute;left:113px;top:240px;font-size:64px;font-weight:700;color:#fff}

.section-title{position:absolute;left:0;width:1200px;top:765px;text-align:center;font-size:62px;font-weight:700;color:var(--ink)}

.filter-bar{position:absolute;left:113px;top:871px;width:975px;height:71px;border:1px solid #e2e2e2;display:flex;align-items:center;padding-left:16px;font-size:17px;color:#666}
.filter-bar span{margin-right:35px}
.filter-bar .all{background:var(--orange);color:#fff;font-weight:700;font-size:15px;padding:12px 17px;margin-right:20px}
.count{position:absolute;left:141px;top:841px;width:33px;height:28px;background:var(--orange);color:#fff;font-size:14px;font-weight:700;text-align:center;line-height:28px}
.count:after{content:"";position:absolute;left:12px;bottom:-6px;border:5px solid transparent;border-top-color:var(--orange);border-bottom:0}

.card{position:absolute;width:313px;height:385px;background:#fff;box-shadow:0 2px 8px rgba(0,0,0,.15);text-align:center}
.card .photo{height:239px;width:100%}
.card h3{margin-top:40px;font-size:26px;font-weight:700}
.card p{margin-top:6px;font-size:20px;color:var(--ink)}
.card .rule{position:absolute;left:0;bottom:0;width:100%;height:5px}

.site-footer{position:absolute;left:0;top:2307px;width:1200px;height:315px;background:var(--footer-bg);border-top:14px solid #f6f6f6}
.foot-brand{position:absolute;left:113px;top:90px;font-size:28px;color:var(--orange);display:flex;align-items:center;gap:10px}
.foot-brand .dot{width:22px;height:22px;border-radius:50%;background:var(--pink)}
.contact{position:absolute;left:113px;top:200px;font-family:'Montserrat',sans-serif;font-size:13px;color:#6a6a6a;line-height:24px}
.contact div{display:flex;align-items:center;gap:8px}
.social{position:absolute;left:537px;top:52px;display:flex;flex-direction:column;gap:10px}
.social i{display:block;width:34px;height:34px;border-radius:50%}
.foot-col{position:absolute;top:40px;width:235px;font-family:'Montserrat',sans-serif}
.foot-col h4{font-size:15px;font-weight:500;color:#222;border-left:3px solid var(--sky);padding-left:14px;line-height:16px;margin-bottom:18px}
.foot-col li{list-style:none;font-size:13px;color:#8a8a8a;line-height:23px;padding:6px 0;border-bottom:1px solid #e6e6e6}
.legal{position:absolute;left:0;top:2622px;width:1200px;height:85px;background:var(--bar);color:#fff;text-align:center;font-size:13px;line-height:85px}
</style>
</head>
<body>

<header class="site-header">
  <div class="brand"><span class="dot"></span>Tallowcrest Care</div>
  <nav class="main-nav">
    <span>Home</span><span>About Us</span><span class="active">What We Do ⌄</span><span>Referrals</span><span>Feedback</span><span>Contact Us</span>
  </nav>
</header>

<section class="hero">
  <div class="hero-photo" role="img" aria-label="Smiling man in a wheelchair working on a laptop in a kitchen"></div>
  <svg width="1200" height="557" viewBox="0 0 1200 557"><polygon points="0,0 368,0 683,557 0,557" fill="#f98e52"/></svg>
  <h1>Vacancies</h1>
</section>

<h2 class="section-title">Vacancies</h2>
<div class="count">8</div>
<div class="filter-bar">
  <span class="all">All</span><span>Penrith</span><span>Mount Druitt</span><span>Casula</span><span>Eastwood</span><span>Baulkham Hills</span><span>Merrylands</span><span>Dharruk</span><span>Plumpton</span>
</div>

<article class="card" style="left:113px;top:991px"><div class="photo" role="img" aria-label="Penrith house with driveway and garage" style="background:linear-gradient(#dfe4ea,#9a948a 60%,#6f8a4e)"></div><h3 style="color:var(--purple)">Penrith</h3><p>4 Bedroom SIL Home</p><i class="rule" style="background:var(--purple)"></i></article>
<article class="card" style="left:443px;top:991px"><div class="photo" role="img" aria-label="Mount Druitt brick house with paved driveway" style="background:linear-gradient(#c9d6e0,#a0563f 50%,#5f9a3c)"></div><h3 style="color:var(--pink)">Mount Druitt</h3><p>4 Bedroom SIL Home</p><i class="rule" style="background:var(--pink)"></i></article>
<article class="card" style="left:773px;top:991px"><div class="photo" role="img" aria-label="Casula house under blue sky" style="background:linear-gradient(#3b9ee8,#d9c79c 60%,#8fae58)"></div><h3 style="color:var(--sky)">Casula</h3><p>4 Bedroom SIL Home</p><i class="rule" style="background:var(--sky)"></i></article>

<article class="card" style="left:113px;top:1410px"><div class="photo" role="img" aria-label="Eastwood cottage with blue shutters" style="background:linear-gradient(#cfe0ee,#d8bea3 50%,#77a04a)"></div><h3 style="color:var(--amber)">Eastwood</h3><p>4 Bedroom SIL Home</p><i class="rule" style="background:var(--amber)"></i></article>
<article class="card" style="left:443px;top:1410px"><div class="photo" role="img" aria-label="Baulkham Hills house with palm tree and lawn" style="background:linear-gradient(#7fbff0,#c9b79a 50%,#4fa53a)"></div><h3 style="color:var(--teal)">Baulkham Hills</h3><p>4 Bedroom SIL Home</p><i class="rule" style="background:var(--teal)"></i></article>
<article class="card" style="left:773px;top:1410px"><div class="photo" role="img" aria-label="Merrylands brick house with long driveway" style="background:linear-gradient(#5aa8ec,#c0703f 45%,#8bbd4c)"></div><h3 style="color:var(--rose)">Merrylands</h3><p>4 Bedroom SIL Home</p><i class="rule" style="background:var(--rose)"></i></article>

<article class="card" style="left:113px;top:1829px"><div class="photo" role="img" aria-label="Dharruk two-storey grey house" style="background:linear-gradient(#c5d8e8,#7b8796 50%,#4f8f2e)"></div><h3 style="color:var(--purple)">Dharruk</h3><p>4 Bedroom SIL Home</p><i class="rule" style="background:var(--purple)"></i></article>
<article class="card" style="left:443px;top:1829px"><div class="photo" role="img" aria-label="Plumpton two-storey brick house" style="background:linear-gradient(#7da36a,#9a4a35 50%,#4a8f2a)"></div><h3 style="color:var(--sky)">Plumpton</h3><p>4 Bedroom SIL Home</p><i class="rule" style="background:var(--sky)"></i></article>

<footer class="site-footer">
  <div class="foot-brand"><span class="dot"></span>Tallowcrest Care</div>
  <div class="contact">
    <div><svg width="14" height="12" viewBox="0 0 14 12"><rect x="1" y="1" width="12" height="10" fill="none" stroke="#ea3d8c" stroke-width="1.5"/><path d="M1 1l6 5 6-5" fill="none" stroke="#ea3d8c" stroke-width="1.5"/></svg>Email: info@tallowcrestcare.com.au</div>
    <div><svg width="14" height="14" viewBox="0 0 14 14"><path d="M3 1l3 3-2 2c1 2 2 3 4 4l2-2 3 3-2 2C6 13 1 8 1 3z" fill="#ea3d8c"/></svg>Phone: +61 0412 385 604</div>
    <div><svg width="14" height="14" viewBox="0 0 14 14"><circle cx="7" cy="7" r="6" fill="none" stroke="#ea3d8c" stroke-width="1.5"/><path d="M7 3v4l3 2" fill="none" stroke="#ea3d8c" stroke-width="1.5"/></svg>Operating Hours: 9AM To 5PM Monday - Friday</div>
  </div>
  <div class="social">
    <i style="background:#6b3a8e"></i><i style="background:#1f5fa8"></i><i style="background:#222"></i><i style="background:#1f5fa8"></i>
  </div>
  <div class="foot-col" style="left:632px">
    <h4>ACCOMMODATION</h4>
    <ul><li>Supported Independent Living (SIL)</li><li>Specialist Disability Accommodation (SDA)</li><li>Short term Accommodation (Respite)</li><li>Vacancies</li></ul>
  </div>
  <div class="foot-col" style="left:892px">
    <h4>WHAT WE DO</h4>
    <ul><li>In Home Care</li><li>Social &amp; Community Services</li><li>Therapeutic Supports</li><li>Support Coordination</li><li>Home Modifications</li></ul>
  </div>
</footer>

<div class="legal">© Copyright 2024 | Tallowcrest Care | All Rights Reserved.</div>

</body>
</html>
```